High end Electrical/home automation Business Card

Need a card for a high end electrical and home automation company utilising the existing logo.
Phone
Email
Website

Like black look with raised detail. Don’t necessarily need to keep colour of logo it could be made grayscale or white etc

Target Market(s)

High end clients

Contact Information for Business Card

Brightmoor Electrical

Requirements
Must have
• Logo, phone, email, website, address

High end look
Nice to have
• Black background card
Raised font
Should not have
• Lots of colour

```html
<!DOCTYPE html>
<html lang="en">
<head>
<meta charset="utf-8">
<title>Brightmoor Electrical – Business Card</title>
<link href="https://fonts.googleapis.com/css2?family=Lato:wght@400;700&display=swap" rel="stylesheet">
<style>
  :root {
    --backdrop: #d4d4d6;
    --card: #141416;
    --card-edge: #1c1c1f;
    --ink: #f2f2f2;
    --ink-soft: #cfcfd2;
    --accent: #1a82d6;
    --pattern-a: #1b1b1e;
    --pattern-b: #232327;
  }
  * { box-sizing: border-box; margin: 0; padding: 0; }
  html, body {
    width: 1200px; height: 800px; overflow: hidden;
    background: var(--backdrop);
    font-family: "Lato", Arial, sans-serif;
  }
  .stage {
    width: 1200px; height: 800px;
    display: flex; align-items: center; justify-content: center; gap: 40px;
  }
  .card {
    position: relative;
    width: 540px; height: 309px;
    background: var(--card);
    border-radius: 4px;
    overflow: hidden;
    color: var(--ink);
  }

  /* Front face */
  .front { background: linear-gradient(135deg, var(--card-edge), var(--card)); }
  .front .brand {
    position: absolute; left: 36px; top: 48px; width: 260px;
    display: flex; flex-direction: column; align-items: flex-start; gap: 12px;
  }
  .brand-dot {
    width: 40px; height: 40px; border-radius: 50%;
    background: var(--accent);
  }
  .brand-name {
    font-weight: 700; font-size: 24px; letter-spacing: -0.2px;
    color: var(--ink); line-height: 1; white-space: nowrap;
  }
  .person {
    position: absolute; right: 36px; top: 60px; width: 200px; text-align: right;
  }
  .person-name {
    font-weight: 400; font-size: 20px; color: var(--accent);
    letter-spacing: 0.5px; text-transform: uppercase; white-space: nowrap;
  }
  .person-title { font-size: 14px; color: var(--ink-soft); margin-top: 2px; }
  .divider {
    position: absolute; left: 30px; right: 30px; top: 168px;
    height: 1px; background: var(--accent);
  }
  .contact {
    position: absolute; left: 36px; bottom: 28px;
    list-style: none; font-size: 13px; line-height: 1.55; color: var(--ink);
  }
  .contact li { display: flex; align-items: center; gap: 9px; white-space: nowrap; }
  .contact svg { width: 12px; height: 12px; fill: var(--accent); flex: none; }
  .address {
    position: absolute; right: 36px; top: 184px;
    font-size: 13px; line-height: 1.55; text-align: right; color: var(--ink);
    font-style: normal; white-space: nowrap;
  }

  /* Back face */
  .back .pattern {
    position: absolute; inset: 0;
    background: linear-gradient(160deg, var(--pattern-b), var(--pattern-a) 60%, var(--card));
  }
  .back .brand {
    position: absolute; left: 40px; bottom: 62px;
    display: flex; align-items: center; gap: 12px;
  }
  .back .brand-dot { width: 36px; height: 36px; }
  .back .brand-name { font-size: 32px; }
  .back .web {
    position: absolute; left: 40px; bottom: 36px;
    font-size: 12px; letter-spacing: 4px; color: var(--ink-soft);
  }
</style>
</head>
<body>
<main class="stage">
  <section class="card front" aria-label="Card front">
    <div class="brand">
      <span class="brand-dot"></span>
      <span class="brand-name">Brightmoor Electrical</span>
    </div>
    <div class="person">
      <p class="person-name">Daniel Harper</p>
      <p class="person-title">President</p>
    </div>
    <div class="divider"></div>
    <address class="address">
      Brightmoor Electrical LLC<br>
      412 Larkspur Road<br>
      Fairbanks, Alaska 99701
    </address>
    <ul class="contact">
      <li><svg viewBox="0 0 24 24"><path d="M6.6 10.8a15 15 0 0 0 6.6 6.6l2.2-2.2a1 1 0 0 1 1-.25 11.4 11.4 0 0 0 3.6.57 1 1 0 0 1 1 1V20a1 1 0 0 1-1 1A17 17 0 0 1 3 4a1 1 0 0 1 1-1h3.5a1 1 0 0 1 1 1c0 1.25.2 2.45.57 3.57a1 1 0 0 1-.25 1z"/></svg>555-214-0937</li>
      <li><svg viewBox="0 0 24 24"><path d="M2 5h20v14H2z"/></svg>info@brightmoorelectrical.com</li>
      <li><svg viewBox="0 0 24 24"><circle cx="12" cy="12" r="10"/></svg>www.brightmoorelectrical.com</li>
    </ul>
  </section>

  <section class="card back" aria-label="Card back">
    <div class="pattern" role="img" aria-label="Subtle raised tonal pattern across the black card"></div>
    <div class="brand">
      <span class="brand-dot"></span>
      <span class="brand-name">Brightmoor Electrical</span>
    </div>
    <p class="web">www.brightmoorelectrical.com</p>
  </section>
</main>
</body>
</html>
```